Road Construction Company needs business cards

We would like a new business card designed for our business.

We're a road construction company based in Qld, Australia.

Can the business card please have the following information on it.

Name: Warren Halbeck
Position: General Manager
Phone: 0472 915 348
Email: Warren.halbeck@tovrin.com.au
Address: 87 Marrow Ave, Pendlebay, QLD, 4023
Website: www.tovrin.com.au

Visually we'd like the card to be professional and simple.

Attached is our logo.

Our website is www.tovrin.com.au

Target Market(s)

Men aged 25-60

Contact Information for Business Card

As listed in project description

Font styles to use
Serif

Requirements
Must have
• Large logo on back of card

```html
<!DOCTYPE html>
<html lang="en">
<head>
<meta charset="utf-8">
<title>Tovrin Road Construction – Business Cards</title>
<link rel="stylesheet" href="https://fonts.googleapis.com/css2?family=Open+Sans:wght@400;600;700&display=swap">
<style>
  :root {
    --stage: #e9eaec;
    --card-dark: #202125;
    --brand-blue: #1557a8;
    --sky-blue: #45abdc;
    --text-light: #ffffff;
    --divider: #9a9ca3;
  }
  * { box-sizing: border-box; margin: 0; padding: 0; }
  html, body { width: 1200px; height: 780px; overflow: hidden; }
  body {
    background: var(--stage);
    font-family: "Open Sans", Arial, sans-serif;
    position: relative;
  }
  .card {
    position: absolute;
    top: 230px;
    width: 560px;
    height: 320px;
    border-radius: 18px;
    overflow: hidden;
    background: var(--card-dark);
    box-shadow: 0 10px 24px rgba(0,0,0,0.25);
  }
  .card--front { left: 26px; }
  .card--back { left: 614px; }
  .card__shapes { position: absolute; inset: 0; width: 100%; height: 100%; }
  .shape-blue { fill: var(--brand-blue); }
  .shape-sky { fill: var(--sky-blue); }

  .company-name {
    position: absolute;
    display: flex;
    align-items: center;
    color: var(--brand-blue);
    font-weight: 700;
    line-height: 1.15;
  }
  .company-name__mark {
    flex: none;
    background: var(--sky-blue);
  }
  .card--front .company-name {
    left: 0; right: 0; top: 140px;
    justify-content: center;
    gap: 14px;
    font-size: 30px;
    white-space: nowrap;
  }
  .card--front .company-name__mark { width: 22px; height: 22px; }
  .card--back .company-name {
    left: 48px; top: 160px;
    width: 205px;
    gap: 10px;
    font-size: 20px;
  }
  .card--back .company-name__mark { width: 14px; height: 14px; }

  .divider {
    position: absolute;
    left: 268px; top: 60px;
    width: 1px; height: 150px;
    background: var(--divider);
  }
  .contact {
    position: absolute;
    left: 296px; top: 58px;
    color: var(--text-light);
  }
  .contact__name {
    color: var(--sky-blue);
    font-size: 25px;
    font-weight: 700;
    line-height: 1.1;
  }
  .contact__role {
    font-size: 13px;
    font-weight: 600;
    margin-bottom: 22px;
  }
  .contact__list { list-style: none; font-size: 12px; line-height: 1.75; }
  .contact__list li { display: flex; align-items: center; gap: 8px; }
  .contact__list svg { width: 12px; height: 12px; fill: var(--sky-blue); flex: none; }
  .address {
    position: absolute;
    left: 210px; bottom: 34px;
    color: var(--text-light);
    font-size: 14px;
  }
</style>
</head>
<body>

<section class="card card--front" aria-label="Card front">
  <svg class="card__shapes" viewBox="0 0 560 320" aria-hidden="true">
    <path class="shape-blue" d="M0,0 L165,0 C85,50 30,130 0,250 Z"/>
    <path class="shape-sky" d="M560,70 L560,320 L430,320 C510,270 545,170 560,70 Z"/>
  </svg>
  <h1 class="company-name"><span class="company-name__mark"></span>Tovrin Road Construction</h1>
</section>

<section class="card card--back" aria-label="Card back">
  <svg class="card__shapes" viewBox="0 0 560 320" aria-hidden="true">
    <path class="shape-blue" d="M0,0 L165,0 C85,50 30,130 0,250 Z"/>
    <path class="shape-sky" d="M560,70 L560,320 L430,320 C510,270 545,170 560,70 Z"/>
  </svg>
  <h2 class="company-name"><span class="company-name__mark"></span>Tovrin Road Construction</h2>
  <div class="divider"></div>
  <div class="contact">
    <p class="contact__name">Warren Halbeck</p>
    <p class="contact__role">General Manager</p>
    <ul class="contact__list">
      <li><svg viewBox="0 0 24 24"><path d="M6.6 10.8a15.1 15.1 0 0 0 6.6 6.6l2.2-2.2a1 1 0 0 1 1-.25 11.4 11.4 0 0 0 3.6.57 1 1 0 0 1 1 1V20a1 1 0 0 1-1 1A17 17 0 0 1 3 4a1 1 0 0 1 1-1h3.5a1 1 0 0 1 1 1c0 1.25.2 2.45.57 3.57a1 1 0 0 1-.25 1z"/></svg>0472 915 348</li>
      <li><svg viewBox="0 0 24 24"><circle cx="12" cy="12" r="10"/></svg>www.tovrin.com.au</li>
      <li><svg viewBox="0 0 24 24"><path d="M2 5h20v14H2z M4 7v.5l8 5 8-5V7z" fill-rule="evenodd"/></svg>Warren.halbeck@tovrin.com.au</li>
    </ul>
  </div>
  <p class="address">87 Marrow Ave, Pendlebay, QLD, 4023</p>
</section>

</body>
</html>
```